business card deign

Logo needs the following on it.
1. attached logo
2. Tagline - "If it keeps a drink cold or the party going...we do it!"
3. Name- Dalton Pikes, Founder and CPO
4. Address - 412 E. Carver Avenue, Ste 2207, Tampa, FL. 33917
5. Phone - 555.318.4726

```html
<!DOCTYPE html>
<html lang="en">
<head>
<meta charset="utf-8">
<title>Bramly Business Card</title>
<link href="https://fonts.googleapis.com/css2?family=Roboto:wght@400;700&display=swap" rel="stylesheet">
<style>
  :root {
    --stage: #232323;
    --card: #161616;
    --card-edge: #0c0c0c;
    --ink: #ffffff;
    --ink-soft: #e6e6e6;
  }
  html, body {
    margin: 0;
    padding: 0;
    width: 1200px;
    height: 711px;
    overflow: hidden;
    background: var(--stage);
    font-family: "Roboto", Arial, sans-serif;
    color: var(--ink);
  }
  .canvas {
    position: relative;
    width: 1200px;
    height: 711px;
  }
  .card {
    position: absolute;
    top: 205px;
    width: 520px;
    height: 300px;
    background: var(--card);
    border-radius: 22px;
    box-shadow: 0 6px 0 var(--card-edge), 0 18px 40px rgba(0,0,0,0.55);
    overflow: hidden;
  }
  .card--front { left: 60px; }
  .card--back { left: 620px; }

  /* Brand name */
  .brand {
    display: flex;
    align-items: center;
  }
  .brand-mark {
    flex: none;
    background: var(--ink);
    border-radius: 50%;
  }
  .brand-name {
    font-weight: 700;
    letter-spacing: 0;
    color: var(--ink);
    line-height: 1;
  }

  /* Front */
  .front-brand {
    position: absolute;
    inset: 0;
    justify-content: center;
    gap: 14px;
  }
  .front-brand .brand-mark { width: 22px; height: 22px; }
  .front-brand .brand-name { font-size: 44px; }

  /* Back */
  .back-brand {
    position: absolute;
    left: 40px;
    top: 36px;
    gap: 9px;
  }
  .back-brand .brand-mark { width: 13px; height: 13px; }
  .back-brand .brand-name { font-size: 24px; }

  .identity {
    position: absolute;
    left: 40px;
    top: 98px;
    display: flex;
    gap: 12px;
  }
  .identity-bar {
    width: 10px;
    background: var(--ink);
  }
  .person-name {
    margin: 0;
    font-size: 26px;
    font-weight: 700;
    line-height: 1.1;
  }
  .person-title {
    margin: 4px 0 0;
    font-size: 14px;
    font-weight: 400;
    color: var(--ink-soft);
  }
  .tagline {
    position: absolute;
    left: 62px;
    top: 170px;
    margin: 0;
    font-size: 11.5px;
    line-height: 1.45;
    color: var(--ink-soft);
    width: 200px;
  }
  .contact {
    position: absolute;
    left: 62px;
    top: 218px;
    margin: 0;
    padding: 0;
    list-style: none;
    font-size: 11.5px;
    line-height: 1.45;
    color: var(--ink-soft);
  }
  .contact li {
    display: flex;
    align-items: flex-start;
    gap: 8px;
    margin-bottom: 4px;
  }
  .contact svg {
    flex: none;
    width: 12px;
    height: 12px;
    margin-top: 2px;
  }
</style>
</head>
<body>
<main class="canvas">
  <section class="card card--front" aria-label="Card front">
    <div class="brand front-brand">
      <span class="brand-mark" aria-hidden="true"></span>
      <span class="brand-name">Bramly</span>
    </div>
  </section>

  <section class="card card--back" aria-label="Card back">
    <div class="brand back-brand">
      <span class="brand-mark" aria-hidden="true"></span>
      <span class="brand-name">Bramly</span>
    </div>
    <div class="identity">
      <span class="identity-bar" aria-hidden="true"></span>
      <div>
        <h1 class="person-name">Dalton Pikes</h1>
        <p class="person-title">Founder and CPO</p>
      </div>
    </div>
    <p class="tagline">If it keeps a drink cold or<br>the party going...we do it!</p>
    <ul class="contact">
      <li>
        <svg viewBox="0 0 24 24" aria-hidden="true"><path fill="none" stroke="#fff" stroke-width="2" d="M5 3h4l2 5-2.5 1.5a11 11 0 0 0 6 6L16 13l5 2v4a2 2 0 0 1-2 2A16 16 0 0 1 3 5a2 2 0 0 1 2-2z"/></svg>
        <span>555.318.4726</span>
      </li>
      <li>
        <svg viewBox="0 0 24 24" aria-hidden="true"><path fill="none" stroke="#fff" stroke-width="2" d="M12 22s7-7 7-12a7 7 0 0 0-14 0c0 5 7 12 7 12z"/><circle cx="12" cy="10" r="2.5" fill="none" stroke="#fff" stroke-width="2"/></svg>
        <span>412 E. Carver Avenue,<br>Ste 2207, Tampa, FL. 33917</span>
      </li>
    </ul>
  </section>
</main>
</body>
</html>
```